Harlow Advisory, Business Cards for International Development Consultancy

I'm an independent consultant working in the international development sector. I work with small organisations in developing countries to help them develop their community based programs so that they can be internationally competitive. This means they need to work better with their own communities to deliver meaningful quality work and also improve the accountability of their work so that they can compete for international and domestic funding.

I like the idea of being a connector between community, local organisations and international best practice and back again (ie acknowledging that international best practice can learn a lot from community).

My surname is Harlow - so I'd like the logo to use the idea of web as a connector.

I work with people with sight impairments - would like my card to be useful for low vision (i.e. clear graphics, easy to read font) and no vision (i.e. brail).

Target Market(s)

international non-government organisations (i.e. pelmark, lift the hamlets, kindred arc), Blue Shield Gold Lantern, government (i.e. Australian Bureau of Overseas Relations, consulars), non government agencies,

Industry/Entity Type

Business

Contact Information for Business Card

International Development Consultant
Linking Global Practice with Local Communities

Marcia Harlow
Lead Consultant
Phone: +61 412 583720
Email: mharlow.advisory@postnest.example

Font styles to use
Sans Serif

Colors
eaf1f7
85acd3
d3a5cc
0456a4
a64599
0255a3

Requirements
Nice to have
• brail
Should not have
• fancy fonts - needs to be easy to read.

```html
<!DOCTYPE html>
<html lang="en">
<head>
<meta charset="utf-8">
<title>Harlow Advisory – Business Cards</title>
<link rel="stylesheet" href="https://fonts.googleapis.com/css2?family=Questrial&display=swap">
<style>
  :root {
    --backdrop: #e8e3d9;
    --paper: #f3f2ef;
    --ink: #1d1d1f;
    --accent: #0456a4;
    --accent-light: #85acd3;
    --accent-pale: #c9d9ec;
    --card-blue: #1f5aa6;
    --silver: #cfd4dc;
  }
  * { box-sizing: border-box; margin: 0; padding: 0; }
  html, body {
    width: 1200px; height: 968px; overflow: hidden;
    background: var(--backdrop);
    font-family: "Questrial", "Century Gothic", sans-serif;
  }
  .canvas { position: relative; width: 1200px; height: 968px; }
  .card {
    position: absolute; left: 270px;
    width: 660px; height: 378px;
    border-radius: 30px; overflow: hidden;
    box-shadow: 0 6px 18px rgba(0,0,0,.18);
  }
  .card--front { top: 70px; background: var(--paper); color: var(--ink); }
  .card--back { top: 520px; background: var(--card-blue); }

  .front__decoration {
    position: absolute; top: 0; right: 0; width: 330px; height: 150px;
  }
  .front__name { position: absolute; left: 40px; top: 52px; font-size: 34px; font-weight: 400; letter-spacing: .5px; }
  .front__role { position: absolute; left: 42px; top: 96px; font-size: 18px; color: var(--accent); }
  .front__contacts { position: absolute; left: 42px; top: 136px; list-style: none; }
  .front__contacts li { display: flex; align-items: center; gap: 14px; font-size: 19px; margin-bottom: 14px; }
  .front__contacts svg { width: 28px; height: 20px; fill: var(--accent); }
  .front__brand {
    position: absolute; left: 150px; top: 246px;
    display: flex; align-items: center; gap: 10px;
    font-size: 22px; color: var(--accent);
  }
  .brand__square { width: 18px; height: 18px; background: var(--accent); }
  .front__tagline { position: absolute; left: 42px; bottom: 34px; font-size: 21px; }

  .back__brand {
    position: absolute; inset: 0;
    display: flex; align-items: center; justify-content: center; gap: 18px;
    font-size: 40px; letter-spacing: 6px; text-transform: uppercase;
    color: var(--silver);
  }
  .back__brand .brand__square { width: 30px; height: 30px; background: var(--silver); }
</style>
</head>
<body>
<div class="canvas">
  <section class="card card--front">
    <svg class="front__decoration" viewBox="0 0 330 150" role="img" aria-label="Decorative striped band motif in pale blue">
      <polygon points="20,0 330,0 330,150 240,150" fill="var(--accent-pale)"/>
    </svg>
    <h1 class="front__name">Marcia Harlow</h1>
    <p class="front__role">Lead Consultant</p>
    <ul class="front__contacts">
      <li>
        <svg viewBox="0 0 28 20" aria-hidden="true"><path d="M1 2h26v16H1z M1 2l13 10 13-10" fill="var(--accent)" stroke="#fff" stroke-width="1.5"/></svg>
        +61 412 583720
      </li>
      <li>
        <svg viewBox="0 0 28 20" aria-hidden="true"><path d="M2 7c0-4 24-4 24 0v2h-6V6H8v3H2z M6 10h16l2 9H4z"/><circle cx="14" cy="14" r="2.5" fill="#fff"/></svg>
        mharlow.advisory@postnest.example
      </li>
    </ul>
    <div class="front__brand"><span class="brand__square"></span>Harlow Advisory</div>
    <p class="front__tagline">Linking Global Practice with Local Communities</p>
  </section>

  <section class="card card--back">
    <div class="back__brand"><span class="brand__square"></span>Harlow Advisory</div>
  </section>
</div>
</body>
</html>
```